Kestrel Facilities Business Card Design

We would now like to design business cards with the new Kestrel Facilities logo

Target Market(s)

Professional

Industry/Entity Type

Professional services

Contact Information for Business Card

Employee name, title, phone number, email address, corporate office address and logo.

Font styles to use
Sans Serif

Colors
0054AA
0677BA
7BADD7
CADEEF
E8F1F8

Requirements
Must have
• My logo
Should not have
• any other pictures or images besides my logo

```html
<!DOCTYPE html>
<html lang="en">
<head>
<meta charset="utf-8">
<title>Kestrel Facilities – Business Card</title>
<link rel="stylesheet" href="https://fonts.googleapis.com/css2?family=Jost:wght@400;500&family=Oswald:wght@500&display=swap">
<style>
  :root {
    --backdrop: #2a2624;
    --card: #0d0d0d;
    --accent: #0a7be6;
    --ink: #f2f2f2;
  }
  * { box-sizing: border-box; margin: 0; padding: 0; }
  html, body {
    width: 1200px; height: 842px; overflow: hidden;
    background: var(--backdrop);
  }
  .canvas {
    position: relative; width: 1200px; height: 842px;
    display: flex; align-items: center; justify-content: center; gap: 60px;
  }
  .card {
    position: relative; width: 510px; height: 292px;
    background: var(--card);
    box-shadow: 0 10px 30px rgba(0,0,0,.45);
    overflow: hidden;
  }
  /* Contact side */
  .band {
    position: absolute; left: 0; right: 0; height: 11px;
    background: var(--accent);
  }
  .band--top { top: 0; }
  .band--bottom { bottom: 16px; }
  .contact {
    position: absolute; inset: 0;
    display: flex; flex-direction: column; align-items: center; justify-content: center;
    text-align: center;
    font-family: "Jost", sans-serif; color: var(--ink);
    letter-spacing: .06em; text-transform: uppercase;
    padding-bottom: 6px;
  }
  .contact__name {
    font-family: "Oswald", sans-serif; font-weight: 500;
    font-size: 30px; line-height: 1; color: var(--accent); letter-spacing: .01em;
  }
  .contact__title { font-size: 13px; margin-top: 2px; }
  .divider { width: 46px; height: 2px; background: var(--accent); margin: 10px 0; }
  .contact__line { font-size: 14px; line-height: 1.3; }
  .contact__line .highlight { color: var(--accent); }
  /* Logo side */
  .tab {
    position: absolute; background: var(--accent);
  }
  .tab--left { left: 0; top: 120px; width: 24px; height: 52px; }
  .tab--right { right: 0; top: 34px; width: 24px; height: 52px; }
  .brand {
    position: absolute; inset: 0;
    display: flex; align-items: center; justify-content: center; gap: 14px;
    font-family: "Jost", sans-serif; font-weight: 500;
    font-size: 34px; color: var(--accent); letter-spacing: .04em; text-transform: uppercase;
  }
  .brand__mark { width: 34px; height: 34px; background: var(--accent); }
</style>
</head>
<body>
<main class="canvas">
  <section class="card card--contact">
    <div class="band band--top"></div>
    <div class="band band--bottom"></div>
    <div class="contact">
      <p class="contact__name">Marcus Hale</p>
      <p class="contact__title">Managing Director</p>
      <div class="divider"></div>
      <p class="contact__line">044-555 010 234</p>
      <p class="contact__line">info@kestrelfm.com</p>
      <p class="contact__line">www.<span class="highlight">kestrelfm</span>.com</p>
      <div class="divider"></div>
      <p class="contact__line">18 Harbour Row, Suite 4</p>
      <p class="contact__line">40210, Northbridge</p>
    </div>
  </section>

  <section class="card card--brand">
    <div class="tab tab--left"></div>
    <div class="tab tab--right"></div>
    <div class="brand">
      <span class="brand__mark"></span>
      <span class="brand__name">Kestrel Facilities</span>
    </div>
  </section>
</main>
</body>
</html>
```